Business Card & Email Signature Design || Upmarket + Luxury

Rima Vale Honey, a New Zealand Manuka Honey company needs a Business Card & Email Signature design.

Our logo's are attached in Gold & Black versions, feel free to be creative with how you use the logo and it's patterns in your design.

Style:
- Looking for an Elegant, Luxurious, Upmarket feel.
- Black/Matte Black Card, Gold Foil, UV Embossing

Information to Add:

- Logo
- Company Name: Rima Vale Honey
- Name: Martin Holloway
- Title: Creative Director
- Phone: +64 2815 96 417
- Email: martin@rimavalehoney.example.nz
- Website: www.rimavalehoney.example.nz

- Socials: ***For email Signature Only***
- Facebook: https://www.facebook.com/rimavalehoney/
- Instagram: https://www.instagram.com/rimavalehoney/

Target Market(s)

Asia/Europe Luxury, Upmarket

Contact Information for Business Card

- Logo
- Name: Martin Holloway
- Phone: +64 2815 96 417

Font styles to use
Other font styles liked:
• Champagne & Limousines (Attached)

Requirements
Must have
• Business Card & Email Signature Design.

Looking for a Sleek, Luxury, Upmarket Design.

```html
<!DOCTYPE html>
<html lang="en">
<head>
<meta charset="utf-8">
<title>Rima Vale Honey — Business Card</title>
<link rel="stylesheet" href="https://fonts.googleapis.com/css2?family=Montserrat:wght@400;600&display=swap">
<style>
  :root {
    --backdrop: #4a4a4a;
    --card: #2f2f2f;
    --card-edge: #3a3a3a;
    --gold: #cdb06f;
    --gold-soft: #bfa263;
    --mark-ring: #1e1e1e;
    --bar-gold: #e0a20d;
    --bar-green: #7cab1a;
    --bar-blue: #1a8fc9;
    --bar-purple: #6b2f95;
  }
  * { box-sizing: border-box; margin: 0; padding: 0; }
  html, body {
    width: 963px;
    height: 1200px;
    overflow: hidden;
    background: var(--backdrop);
    font-family: "Montserrat", sans-serif;
  }
  .canvas { position: relative; width: 963px; height: 1200px; }
  .card {
    position: absolute;
    left: 232px;
    width: 556px;
    height: 316px;
    background: var(--card);
    border: 1px solid var(--card-edge);
  }
  .card--front { top: 222px; }
  .card--back { top: 637px; }

  .contact { position: absolute; left: 42px; top: 154px; color: var(--gold); }
  .contact__name { font-weight: 600; font-size: 20px; letter-spacing: 0.02em; line-height: 1; }
  .contact__title { font-weight: 400; font-size: 13px; color: var(--gold-soft); margin-top: 5px; letter-spacing: 0.03em; }
  .contact__bars { display: flex; gap: 3px; margin-top: 14px; }
  .contact__bars span { width: 30px; height: 2px; }
  .bar--gold { background: var(--bar-gold); }
  .bar--green { background: var(--bar-green); }
  .bar--blue { background: var(--bar-blue); }
  .bar--purple { background: var(--bar-purple); }
  .contact__lines { list-style: none; margin-top: 14px; font-size: 12.5px; line-height: 18px; color: var(--gold-soft); }

  .front-mark {
    position: absolute;
    left: 264px;
    top: 28px;
    width: 250px;
    height: 250px;
    border-radius: 50%;
    border: 2px solid var(--mark-ring);
    display: flex;
    align-items: center;
    justify-content: center;
  }
  .front-mark__name {
    font-size: 15px;
    letter-spacing: 0.18em;
    text-transform: uppercase;
    color: var(--mark-ring);
  }

  .brand {
    position: absolute;
    inset: 0;
    display: flex;
    align-items: center;
    justify-content: center;
    gap: 18px;
  }
  .brand__dot { width: 62px; height: 62px; border-radius: 50%; border: 1.5px solid var(--gold); }
  .brand__words { color: var(--gold); font-weight: 400; text-align: center; }
  .brand__name { font-size: 24px; letter-spacing: 0.16em; line-height: 1; }
  .brand__co { font-size: 12px; letter-spacing: 0.08em; margin-top: 6px; }
</style>
</head>
<body>
  <main class="canvas">
    <section class="card card--front" aria-label="Business card front">
      <div class="contact">
        <h1 class="contact__name">MARTIN HOLLOWAY</h1>
        <p class="contact__title">Creative Director</p>
        <div class="contact__bars" aria-hidden="true">
          <span class="bar--gold"></span><span class="bar--green"></span><span class="bar--blue"></span><span class="bar--purple"></span>
        </div>
        <ul class="contact__lines">
          <li>+64 2815 96 417</li>
          <li>martin@rimavalehoney.example.nz</li>
          <li>www.rimavalehoney.example.nz</li>
        </ul>
      </div>
      <div class="front-mark" role="img" aria-label="Embossed brand mark area">
        <span class="front-mark__name">Rima Vale Honey</span>
      </div>
    </section>

    <section class="card card--back" aria-label="Business card back">
      <div class="brand">
        <span class="brand__dot" aria-hidden="true"></span>
        <div class="brand__words">
          <p class="brand__name">RIMA VALE HONEY</p>
          <p class="brand__co">CO.</p>
        </div>
      </div>
    </section>
  </main>
</body>
</html>
```